TALMORK

The business want a professional looking business card. We have a scetch we will add but want the extra upgrade, and would like more suggestions for variations of our business cards.

```html
<!DOCTYPE html>
<html lang="en">
<head>
<meta charset="UTF-8">
<title>TALMORK Business Card</title>
<link rel="stylesheet" href="https://fonts.googleapis.com/css2?family=Montserrat:wght@400;500;700&display=swap">
<style>
  :root {
    --backdrop: #e6e4df;
    --paper: #f7f4ec;
    --gold: #c0901f;
    --gold-light: #e6c667;
    --gold-dark: #9c7215;
    --ink: #1c1c1c;
    --white: #ffffff;
  }
  * { box-sizing: border-box; margin: 0; padding: 0; }
  html, body {
    width: 1200px; height: 800px; overflow: hidden;
    background: var(--backdrop);
    font-family: "Montserrat", Arial, sans-serif;
  }
  .sheet {
    width: 1200px; height: 800px;
    display: flex; flex-direction: column;
    align-items: center; justify-content: center; gap: 40px;
  }
  .card {
    position: relative;
    width: 600px; height: 343px;
    border-radius: 18px; overflow: hidden;
    box-shadow: 0 6px 18px rgba(0,0,0,.18);
  }
  /* Front */
  .card-front { background: var(--paper); }
  .card-front .waves { position: absolute; inset: 0; width: 100%; height: 100%; }
  .brand {
    position: absolute; left: 0; top: 60px; width: 246px;
    display: flex; flex-direction: column; align-items: center;
  }
  .brand-mark {
    width: 70px; height: 70px; border-radius: 50%;
    background: var(--gold); margin-bottom: 22px;
  }
  .brand-name {
    font-weight: 700; font-size: 34px; letter-spacing: 3px;
    color: var(--gold);
  }
  .brand-since {
    display: flex; align-items: center; gap: 8px; margin-top: 4px;
    font-size: 12px; letter-spacing: 3px; color: #555;
  }
  .brand-since::before, .brand-since::after {
    content: ""; width: 30px; height: 1px; background: var(--gold);
  }
  .divider {
    position: absolute; left: 246px; top: 40px;
    width: 1px; height: 190px; background: var(--gold);
  }
  .details { position: absolute; left: 272px; top: 54px; }
  .details-name {
    font-weight: 700; font-size: 19px; color: var(--gold); letter-spacing: .5px;
  }
  .details-role { font-size: 15px; color: #333; margin-top: 8px; line-height: 1.35; }
  .contacts { list-style: none; margin-top: 22px; }
  .contacts li {
    display: flex; align-items: center; gap: 12px;
    font-size: 13px; color: #222; margin-bottom: 11px;
  }
  .contacts svg { width: 14px; height: 14px; flex: none; }
  /* Back */
  .card-back {
    background: linear-gradient(135deg, var(--gold-dark) 0%, var(--gold) 35%, var(--gold-light) 60%, var(--gold) 100%);
    display: flex; flex-direction: column; align-items: center; justify-content: center;
    color: var(--white);
  }
  .card-back .brand-mark { background: var(--white); margin-bottom: 24px; width: 84px; height: 84px; }
  .card-back .brand-name { color: var(--white); font-size: 44px; letter-spacing: 4px; }
  .card-back .brand-since { color: var(--white); font-size: 14px; }
  .card-back .brand-since::before, .card-back .brand-since::after { background: var(--white); width: 60px; }
</style>
</head>
<body>
<main class="sheet">
  <section class="card card-front">
    <svg class="waves" viewBox="0 0 600 343" preserveAspectRatio="none" aria-hidden="true">
      <defs>
        <linearGradient id="goldBand" x1="0" y1="0" x2="1" y2="1">
          <stop offset="0" stop-color="#a67a18"/>
          <stop offset=".5" stop-color="#e3c262"/>
          <stop offset="1" stop-color="#b48620"/>
        </linearGradient>
      </defs>
      <path d="M0 262 C120 255 200 280 300 282 C420 284 520 240 600 200 L600 343 L0 343 Z" fill="url(#goldBand)"/>
      <path d="M0 250 C80 240 160 262 250 272 C180 272 90 272 0 290 Z" fill="var(--ink)"/>
      <path d="M0 290 C90 272 190 272 280 282 C200 282 90 290 0 304 Z" fill="var(--paper)"/>
      <path d="M260 276 C400 274 520 230 600 170" fill="none" stroke="url(#goldBand)" stroke-width="7"/>
      <path d="M330 280 C450 270 540 230 600 196" fill="none" stroke="var(--paper)" stroke-width="5"/>
    </svg>
    <div class="brand">
      <span class="brand-mark"></span>
      <span class="brand-name">TALMORK</span>
      <span class="brand-since">SINCE 2026</span>
    </div>
    <div class="divider"></div>
    <div class="details">
      <p class="details-name">TALMORK H AALSTAD</p>
      <p class="details-role">CEO &amp; Founder<br>Henrik Aalstad</p>
      <ul class="contacts">
        <li>
          <svg viewBox="0 0 24 24"><path fill="var(--gold)" d="M6.6 10.8a15 15 0 0 0 6.6 6.6l2.2-2.2a1 1 0 0 1 1-.25 11.4 11.4 0 0 0 3.6.57 1 1 0 0 1 1 1V20a1 1 0 0 1-1 1A17 17 0 0 1 3 4a1 1 0 0 1 1-1h3.5a1 1 0 0 1 1 1c0 1.25.2 2.45.57 3.6a1 1 0 0 1-.25 1z"/></svg>
          004791234567
        </li>
        <li>
          <svg viewBox="0 0 24 24"><rect x="2" y="5" width="20" height="14" rx="1" fill="var(--gold)"/><path d="M2 6l10 7 10-7" fill="none" stroke="var(--paper)" stroke-width="1.6"/></svg>
          talmork.llc@mailbox.no
        </li>
        <li>
          <svg viewBox="0 0 24 24" fill="none" stroke="var(--gold)" stroke-width="2"><circle cx="12" cy="12" r="9"/><ellipse cx="12" cy="12" rx="4" ry="9"/><path d="M3 12h18"/></svg>
          www.talmork.llc
        </li>
      </ul>
    </div>
  </section>

  <section class="card card-back">
    <span class="brand-mark"></span>
    <span class="brand-name">TALMORK</span>
    <span class="brand-since">SINCE 2026</span>
  </section>
</main>
</body>
</html>
```